Business Card Design Project

We need a Business Card for an Mechanical Engineering firm in Singapore. The design should be Modern & Technical looking, yet eye catching.

Our company deals in Cutting Tools & Machine Accessories for the Manufacturing Industries such as Oil & Gas, Aero Space, etc... For more information on our Company, you can either email me or view our website www.torvalen.com.sg.

We are trying to revamp our image to give our consumers a fresh new perspective to our company, so we welcome all ideas.

Industry/Entity Type

Business

Requirements
Must have
• Must incorporate New Company Logo into the card as shown in Uploaded file.

```html
<!DOCTYPE html>
<html lang="en">
<head>
<meta charset="utf-8">
<title>Torvalen Tools – Business Card</title>
<link rel="stylesheet" href="https://fonts.googleapis.com/css2?family=Cabin:ital,wght@0,400;0,500;0,600;1,700&display=swap">
<style>
  :root {
    --page-bg: #ece8e4;
    --crimson: #9b1b35;
    --crimson-deep: #8a1a30;
    --maroon-dark: #3f111f;
    --maroon-glow: #8e1a34;
    --ink: #3a2a2a;
    --paper: #ffffff;
  }
  * { box-sizing: border-box; margin: 0; padding: 0; }
  html, body {
    width: 1200px; height: 900px; overflow: hidden;
    background: var(--page-bg);
    font-family: "Cabin", sans-serif;
  }
  .card {
    position: absolute; left: 50px; top: 282px;
    width: 1100px; height: 336px;
    display: flex;
    box-shadow: 0 10px 24px rgba(0,0,0,0.25);
  }
  .card-front {
    position: relative;
    width: 550px; height: 100%;
    background: var(--paper);
    border-left: 10px solid var(--crimson);
  }
  .card-back {
    position: relative;
    flex: 1; height: 100%;
    background: radial-gradient(ellipse 60% 75% at 45% 45%, var(--maroon-glow) 0%, #5c1428 45%, var(--maroon-dark) 100%);
    display: flex; align-items: center; justify-content: center;
  }
  .brand {
    display: flex; align-items: center; gap: 8px;
    font-weight: 600; color: var(--crimson);
    letter-spacing: 0.5px;
  }
  .brand-mark { border-radius: 50%; background: currentColor; flex: none; }
  .brand--small {
    position: absolute; left: 36px; top: 80px;
    font-size: 24px;
  }
  .brand--small .brand-mark { width: 14px; height: 14px; }
  .brand--large { color: #ffffff; font-size: 46px; letter-spacing: 1px; }
  .brand--large .brand-mark { width: 24px; height: 24px; }
  .person {
    position: absolute; left: 36px; top: 137px;
  }
  .person-name {
    font-style: italic; font-weight: 700;
    font-size: 18px; color: var(--crimson-deep);
  }
  .person-role {
    font-size: 15px; color: var(--ink); margin-top: 2px;
  }
  .divider {
    position: absolute; left: 36px; top: 187px;
    width: 265px; height: 1px;
    background: linear-gradient(90deg, var(--crimson) 0%, rgba(155,27,53,0.1) 100%);
  }
  .contacts {
    position: absolute; left: 36px; top: 201px;
    list-style: none;
    font-size: 15px; color: var(--ink);
    line-height: 21px;
  }
  .contacts li { display: flex; align-items: flex-start; gap: 6px; }
  .contacts svg { width: 16px; height: 16px; flex: none; margin-top: 3px; }
</style>
</head>
<body>
  <main class="card">
    <section class="card-front">
      <div class="brand brand--small"><span class="brand-mark"></span>TORVALEN TOOLS</div>

      <div class="person">
        <p class="person-name">Fname Lname</p>
        <p class="person-role">Company Position</p>
      </div>
      <div class="divider"></div>

      <ul class="contacts">
        <li>
          <svg viewBox="0 0 16 16" aria-hidden="true"><rect x="3" y="5" width="10" height="10" rx="1.5" fill="var(--crimson)"/><rect x="5" y="1" width="3" height="5" fill="var(--crimson)"/><rect x="5" y="8" width="6" height="5" fill="#fff"/></svg>
          <span>655-014-2270</span>
        </li>
        <li>
          <svg viewBox="0 0 16 16" aria-hidden="true"><rect x="1.5" y="3.5" width="13" height="9" fill="none" stroke="var(--crimson)" stroke-width="1.4"/><path d="M1.5 3.5 8 9l6.5-5.5M1.5 12.5 6.5 8M14.5 12.5 9.5 8" fill="none" stroke="var(--crimson)" stroke-width="1.2"/></svg>
          <span>name@torvalen.com.sg</span>
        </li>
        <li>
          <svg viewBox="0 0 16 16" aria-hidden="true"><circle cx="8" cy="8" r="6.5" fill="var(--crimson)"/><path d="M1.5 8h13M8 1.5c-3 3-3 10 0 13M8 1.5c3 3 3 10 0 13M3 4.5h10M3 11.5h10" fill="none" stroke="#fff" stroke-width="0.9"/></svg>
          <span>www.torvalen.com.sg</span>
        </li>
        <li>
          <svg viewBox="0 0 16 16" aria-hidden="true"><path d="M1 8 8 2l7 6" fill="none" stroke="var(--crimson)" stroke-width="1.6"/><path d="M3.5 7.5V14h9V7.5" fill="none" stroke="var(--crimson)" stroke-width="1.4"/><rect x="6.5" y="10" width="3" height="4" fill="var(--crimson)"/></svg>
          <span>27 Kestrel Link #03-12, Norvale<br>Business Park, Singapore 609871</span>
        </li>
      </ul>
    </section>

    <section class="card-back">
      <div class="brand brand--large"><span class="brand-mark"></span>TORVALEN TOOLS</div>
    </section>
  </main>
</body>
</html>
```